Loom Harbor needs a website

I sell rugs and carpet on my website, loomharborfloors.example. I need help with the site design to make it "pop". The logo in the header has been designed and I want the site to match it's style and color. Also I have some example sites for layout:
matsquick.example
weave-outlet.example

Industry/Entity Type

Carpet

Requirements
Must have
• Scrolling images on front page. I will insert photos, just need the code.

```html
<!DOCTYPE html>
<html lang="en">
<head>
<meta charset="utf-8">
<title>Loom Harbor — Rugs and Carpets</title>
<link rel="stylesheet" href="https://fonts.googleapis.com/css2?family=Quicksand:wght@300;400;500;600;700&display=swap">
<style>
  :root{
    --ink:#111214;
    --navy:#1d3f6e;
    --blue:#1b4379;
    --green:#5cb25a;
    --green-soft:#8fc98c;
    --paper:#ffffff;
    --mist:#f7f7f7;
    --line:#2a2b2e;
    --muted:#8a8a8a;
  }
  *{box-sizing:border-box;margin:0;padding:0}
  html,body{width:895px;height:1200px;overflow:hidden}
  body{position:relative;background:var(--paper);font-family:"Quicksand",sans-serif;color:var(--ink)}
  .abs{position:absolute}

  .topbar{left:0;top:0;width:895px;height:27px;background:var(--ink)}
  .topbar .social-dot{position:absolute;top:8px;width:11px;height:11px;border-radius:50%;background:#4a4b4f}
  .topbar .switch{position:absolute;top:8px;font-size:9px;color:#8d8e92;font-weight:600}

  .brand{left:128px;top:58px;display:flex;align-items:center;gap:10px}
  .brand .mark{width:26px;height:26px;border-radius:50%;background:var(--navy)}
  .brand .name{font-size:30px;font-weight:600;color:var(--navy);letter-spacing:.5px}

  .account{right:128px;top:45px;text-align:right;font-size:9.5px;letter-spacing:1px}
  .account .welcome{color:#333;font-weight:500}
  .account .welcome b{color:var(--navy);font-weight:700}
  .account .welcome b span{color:var(--green)}
  .account .auth{margin-top:9px;font-weight:700}
  .cart{left:602px;top:112px;font-size:9px;font-weight:700;letter-spacing:1px}
  .basket{left:718px;top:84px}

  .nav{left:128px;top:145px;width:639px;height:63px;background:var(--ink);display:flex}
  .nav a{display:flex;align-items:center;justify-content:center;color:#fff;text-decoration:none;font-size:12px;font-weight:700;letter-spacing:1.3px;border-right:1px solid var(--line)}
  .nav a:last-child{border-right:0}
  .nav a.active{color:var(--green);border-bottom:2px solid var(--green)}

  .photo{background:linear-gradient(135deg,#e9e6e1,#c9c4bd)}
  .hero{left:128px;top:210px;width:410px;height:319px}
  .hero-copy{left:128px;top:290px;width:410px;text-align:center}
  .hero-copy .brandline{font-size:20px;font-weight:700;color:var(--ink);margin-bottom:22px}
  .hero-copy .lead{font-size:24px;font-weight:400;color:var(--navy);letter-spacing:1px;line-height:1}
  .hero-copy .strong{font-size:24px;font-weight:700;color:var(--navy);letter-spacing:1px;margin-top:6px}
  .btn-dark{display:inline-flex;align-items:center;justify-content:center;background:var(--ink);color:#fff;font-size:12px;font-weight:600;letter-spacing:1.3px}
  .hero-btn{left:266px;top:410px;width:134px;height:41px}
  .dots{left:316px;top:465px;display:flex;gap:4px}
  .dots i{width:8px;height:8px;border-radius:50%;background:#fff;display:block}
  .dots i:first-child{background:var(--ink)}

  .promo{text-align:center}
  .promo .title{font-size:27px;font-weight:700;letter-spacing:2px;color:var(--ink)}
  .promo .sub{font-size:12px;font-weight:700;letter-spacing:1px;color:var(--navy)}
  .promo .sub span{color:var(--green)}
  .promo .btn-dark{width:86px;height:29px;font-size:9.5px;margin-top:6px}

  .tile{top:532px;height:129px;display:flex;align-items:center;color:#fff}
  .tile .icon{margin-left:18px;width:64px}
  .tile .label{margin-left:16px;line-height:1.1}
  .tile .label .l1{font-size:20px;font-weight:400;letter-spacing:1.5px}
  .tile .label .l2{font-size:20px;font-weight:700;letter-spacing:1.5px}
  .tile.dark{left:128px;width:210px;background:var(--ink)}
  .tile.blue{left:342px;width:211px;background:var(--blue)}
  .tile.green{left:556px;width:211px;background:var(--green)}

  .categories{left:128px;top:673px;width:209px;height:255px;background:var(--mist)}
  .section-title{font-size:19px;letter-spacing:1.5px;font-weight:500}
  .section-title b{font-weight:700}
  .categories .section-title{text-align:center;margin-top:14px;font-weight:700}
  .cat-label{font-size:8.5px;font-weight:700;letter-spacing:.6px;color:var(--navy)}
  .cat-label span{color:var(--green-soft);font-weight:500}
  .view-more{left:128px;top:928px;width:209px;height:32px;background:var(--ink);color:#fff;font-size:9.5px;font-weight:600;letter-spacing:1px;display:flex;align-items:center;justify-content:center}
  .view-more-tab{left:211px;top:948px;width:43px;height:26px;border-radius:0 0 22px 22px;background:var(--ink)}

  .product .name{font-size:18px;font-weight:700;letter-spacing:1.5px}
  .product .brandline{font-size:12.5px;letter-spacing:1px;color:var(--navy);margin-top:2px}
  .price{height:30px;width:75px;background:var(--ink);color:var(--green);font-size:12px;font-weight:600;display:flex;align-items:center;justify-content:center}
  .add{height:30px;width:34px;background:var(--ink);display:flex;align-items:center;justify-content:center}

  .footer{left:0;top:998px;width:895px;height:159px;background:var(--mist)}
  .fcol{top:1031px}
  .fcol h4{font-size:11.5px;font-weight:700;letter-spacing:1.3px;color:var(--navy);margin-bottom:10px}
  .fcol li{list-style:none;font-size:7.5px;font-weight:600;letter-spacing:.3px;color:#333;line-height:15.5px}
  .fcol .dot{display:inline-block;width:9px;height:9px;border-radius:50%;background:var(--ink);margin-right:9px}
  .email{width:120px;height:26px;border:1px solid #dedede;background:#fff;font-size:7.5px;color:#bbb;letter-spacing:.8px;padding-left:9px;display:flex;align-items:center}
  .subscribe{width:120px;height:24px;background:var(--ink);color:#fff;font-size:8px;font-weight:700;letter-spacing:.8px;display:flex;align-items:center;justify-content:center;margin-top:3px}

  .bottombar{left:0;top:1157px;width:895px;height:43px;background:var(--ink);color:#fff;font-size:8px;font-weight:600;display:flex;align-items:center;justify-content:center;letter-spacing:.3px}
</style>
</head>
<body>

<div class="abs topbar">
  <i class="social-dot" style="left:130px"></i>
  <i class="social-dot" style="left:155px"></i>
  <i class="social-dot" style="left:182px"></i>
  <span class="switch" style="left:720px">EN ⌄</span>
  <span class="switch" style="left:752px">$ ⌄</span>
</div>

<div class="abs brand"><i class="mark"></i><span class="name">loom harbor</span></div>

<div class="abs account">
  <div class="welcome">WELCOME TO THE <b>LOOM <span>HARBOR</span></b></div>
  <div class="auth">LOGIN &nbsp;/&nbsp; SIGN UP</div>
</div>
<div class="abs cart">SHOPPING CART - &nbsp;(0)</div>
<svg class="abs basket" width="50" height="42" viewBox="0 0 50 42" aria-label="Shopping basket" role="img">
  <path d="M15 16 L22 3 M35 16 L28 3" stroke="var(--green)" stroke-width="4" stroke-linecap="round"/>
  <path d="M2 16 H48 L43 40 H7 Z" fill="var(--navy)"/>
  <path d="M14 21 V35 M21 21 V35 M29 21 V35 M36 21 V35" stroke="#fff" stroke-width="2.5"/>
</svg>

<nav class="abs nav">
  <a class="active" style="width:88px">HOME</a>
  <a style="width:104px">ABOUT</a>
  <a style="width:95px">RUGS</a>
  <a style="width:114px">CARPETS</a>
  <a style="width:119px">SERVICES</a>
  <a style="width:119px">CONTACT</a>
</nav>

<div class="abs photo hero" role="img" aria-label="Slideshow photo: bright living room with white sofa, rug and city-view windows" style="background:linear-gradient(120deg,#dcdcd8,#f1efeb 45%,#cfc9c0)"></div>
<div class="abs hero-copy">
  <div class="brandline">loom harbor</div>
  <div class="lead">SELLING BEST</div>
  <div class="strong">RUGS AND CARPETS !</div>
</div>
<div class="abs btn-dark hero-btn">SHOP NOW</div>
<div class="abs dots"><i></i><i></i><i></i></div>

<div class="abs photo" role="img" aria-label="Photo: white lounge with shaggy area rug" style="left:542px;top:210px;width:225px;height:158px;background:linear-gradient(135deg,#cfd3d8,#e8e6e3 55%,#bfb9b3)"></div>
<div class="abs promo" style="left:542px;top:245px;width:225px">
  <div class="title">RUGS</div>
  <div class="sub">LOOM <span>HARBOR</span></div>
  <div class="btn-dark">SHOP NOW</div>
</div>
<div class="abs photo" role="img" aria-label="Photo: modern living room with grey carpet" style="left:542px;top:371px;width:225px;height:158px;background:linear-gradient(135deg,#9a9690,#cfcbc5 55%,#7d7873)"></div>
<div class="abs promo" style="left:542px;top:406px;width:225px">
  <div class="title">CARPETS</div>
  <div class="sub">LOOM <span>HARBOR</span></div>
  <div class="btn-dark">SHOP NOW</div>
</div>

<div class="abs tile dark">
  <svg class="icon" viewBox="0 0 64 40" height="40" aria-hidden="true">
    <rect x="0" y="4" width="38" height="26" fill="#4a4b4f"/>
    <path d="M40 12 H52 L62 22 V30 H40 Z" fill="#4a4b4f"/>
    <circle cx="12" cy="33" r="6" fill="#4a4b4f" stroke="var(--ink)" stroke-width="2"/>
    <circle cx="50" cy="33" r="6" fill="#4a4b4f" stroke="var(--ink)" stroke-width="2"/>
    <text x="19" y="22" font-family="Quicksand,sans-serif" font-size="11" font-weight="700" fill="var(--ink)" text-anchor="middle">FREE</text>
  </svg>
  <div class="label"><div class="l1">Free</div><div class="l2">SHIPPING</div></div>
</div>
<div class="abs tile blue">
  <svg class="icon" viewBox="0 0 64 48" height="48" aria-hidden="true">
    <path d="M18 2 H50 L42 40 H6 Z" fill="#2f6bc0"/>
    <path d="M22 12 H42 M20 20 H40 M18 28 H36" stroke="var(--blue)" stroke-width="3"/>
    <path d="M2 36 Q10 46 30 44" stroke="#2f6bc0" stroke-width="4" fill="none"/>
  </svg>
  <div class="label"><div class="l1">ORDER</div><div class="l2">ONLINE</div></div>
</div>
<div class="abs tile green">
  <svg class="icon" viewBox="0 0 64 48" height="48" aria-hidden="true">
    <path d="M10 18 L30 26 L54 18 V40 L30 48 L10 40 Z" fill="none" stroke="#e5f3e3" stroke-width="3"/>
    <path d="M30 26 V48 M10 18 L2 26 L24 34 L30 26 M54 18 L62 26 L38 34" fill="none" stroke="#e5f3e3" stroke-width="3"/>
    <path d="M32 0 V14 M26 9 L32 15 L38 9" stroke="#e5f3e3" stroke-width="3" fill="none"/>
  </svg>
  <div class="label"><div class="l1">SPECIAL</div><div class="l2">OFFER</div></div>
</div>

<div class="abs categories"><div class="section-title">CATEGORIES</div></div>
<div class="abs photo" role="img" aria-label="Photo: cream area rug on wood floor" style="left:143px;top:722px;width:88px;height:73px;background:linear-gradient(#d9cdb7,#a78a62)"></div>
<div class="abs photo" role="img" aria-label="Photo: red carpet flooring" style="left:234px;top:722px;width:89px;height:73px;background:linear-gradient(#d8d6d1 30%,#c21a33)"></div>
<div class="abs cat-label" style="left:144px;top:801px">Area <span>Rugs</span></div>
<div class="abs cat-label" style="left:235px;top:801px">Carpet <span>Flooring</span></div>
<div class="abs photo" role="img" aria-label="Photo: bedroom with light flooring" style="left:143px;top:823px;width:88px;height:72px;background:linear-gradient(#a7a49f,#e3e0db)"></div>
<div class="abs photo" role="img" aria-label="Photo: commercial lounge area" style="left:234px;top:823px;width:89px;height:72px;background:linear-gradient(#cfc8c1,#8d8680)"></div>
<div class="abs cat-label" style="left:144px;top:902px">Harwood <span>Area</span></div>
<div class="abs cat-label" style="left:235px;top:902px">Commercial <span>Area</span></div>
<div class="abs view-more-tab"></div>
<div class="abs view-more">VIEW MORE</div>
<svg class="abs" style="left:225px;top:958px" width="16" height="9" viewBox="0 0 16 9" aria-hidden="true"><path d="M1 1 L8 7 L15 1" stroke="#fff" stroke-width="1.6" fill="none"/></svg>

<div class="abs section-title" style="left:343px;top:687px">LATEST <b>PRODUCTS</b></div>

<div class="abs photo" role="img" aria-label="Product photo: striped rug in a shelved living room" style="left:345px;top:720px;width:138px;height:153px;background:linear-gradient(#e8e6e3 55%,#b9724a 75%,#d8d4cf)"></div>
<div class="abs photo" role="img" aria-label="Product photo: carpeted lounge with white sofa" style="left:487px;top:720px;width:138px;height:153px;background:linear-gradient(135deg,#b9a58a,#e9e3da 60%,#8a7a68)"></div>
<div class="abs photo" role="img" aria-label="Product photo: white rug in a sunny living room" style="left:629px;top:720px;width:138px;height:153px;background:linear-gradient(135deg,#eeeeec,#d9dadb 60%,#f4f3f1)"></div>

<div class="abs product" style="left:344px;top:884px"><div class="name">RUGS</div><div class="brandline">LOOM <span style="color:var(--green)">HARBOR</span></div></div>
<div class="abs product" style="left:487px;top:884px"><div class="name">CARPETS</div><div class="brandline">LOOM <span style="color:var(--green)">HARBOR</span></div></div>
<div class="abs product" style="left:628px;top:884px"><div class="name">RUGS</div><div class="brandline">LOOM <span style="color:var(--green)">HARBOR</span></div></div>

<div class="abs price" style="left:345px;top:930px">$ 23.89</div>
<div class="abs add" style="left:423px;top:930px"><svg width="18" height="16" viewBox="0 0 18 16" aria-hidden="true"><path d="M1 1 H4 L6 10 H15 L17 4 H5" stroke="#fff" stroke-width="1.6" fill="none"/><circle cx="7" cy="13.5" r="1.5" fill="#fff"/><circle cx="14" cy="13.5" r="1.5" fill="#fff"/></svg></div>
<div class="abs price" style="left:487px;top:930px">$ 23.89</div>
<div class="abs add" style="left:565px;top:930px"><svg width="18" height="16" viewBox="0 0 18 16" aria-hidden="true"><path d="M1 1 H4 L6 10 H15 L17 4 H5" stroke="#fff" stroke-width="1.6" fill="none"/><circle cx="7" cy="13.5" r="1.5" fill="#fff"/><circle cx="14" cy="13.5" r="1.5" fill="#fff"/></svg></div>
<div class="abs price" style="left:629px;top:930px">$ 23.89</div>
<div class="abs add" style="left:707px;top:930px"><svg width="18" height="16" viewBox="0 0 18 16" aria-hidden="true"><path d="M1 1 H4 L6 10 H15 L17 4 H5" stroke="#fff" stroke-width="1.6" fill="none"/><circle cx="7" cy="13.5" r="1.5" fill="#fff"/><circle cx="14" cy="13.5" r="1.5" fill="#fff"/></svg></div>

<footer class="abs footer"></footer>
<div class="abs fcol" style="left:128px"><h4>MENU</h4><ul><li>HOME</li><li>ABOUT</li><li>RUGS</li><li>CARPETS</li><li>CONTACT</li></ul></div>
<div class="abs fcol" style="left:231px"><h4>MY ACCOUNT</h4><ul><li>LOGIN</li><li>REGISTER</li><li>SIGN UP</li><li>CHECKOUT</li></ul></div>
<div class="abs fcol" style="left:381px"><h4>INFORMATION</h4><ul><li>PRIVACY POLICY</li><li>SITEMAP</li><li>TERMS &amp; CONDITION</li></ul></div>
<div class="abs fcol" style="left:531px"><h4>SOCIAL</h4><div><i class="dot"></i><i class="dot"></i><i class="dot"></i></div></div>
<div class="abs fcol" style="left:647px"><h4>NEWSLETTER</h4><div class="email">E-MAIL</div><div class="subscribe">SUBSCRIBE</div></div>

<div class="abs bottombar">Copyrights © 2014 Loom Harbor, LLC</div>

</body>
</html>
```